Brackenford Fluidworks needs a website describing the repair business we are in.

Brackenford Fluidworks is a full hydraulic repair facility. We have 2 shops. We repair and service all hydraulic cylinders, pneumatic cylinders, hydraulic pumps, motors, valves and gearboxes. Our services range from large industrial plants to the individual that owns one piece of equipment. We also offer removal and install of cylinders. Along with free pick up and delivery, within a certain distance which is usually 100 miles from one of our shops.

With over 30 years experience in the hydraulic business, we can repair or replace any job. There is not a job too big or too small, we service them all.

We have customers that send whole pieces of equipment to us to do complete overhauls on all the hydraulics. Ranging from a country club green roller to a 10 ton boom truck.

Target Market(s)

Industrial plants, road builders, dirt work companies, general contractors, owners of industrial equipment (bulldozers, excavators, loaders, scrapers, motor graders, etc.

Industry/Entity Type

Hydraulic

Number of Pages Required

5+ page

Font styles to use
Sans Serif

Colors
ec1f27
ffffff
aaaaaa

Requirements
Must have
• Information about what we offer and pictures of jobs completed.
Nice to have
• Nice stock photos of jobsites and industrial plants.
Should not have
• Any sort of comical characters.

```html
<!DOCTYPE html>
<html lang="en">
<head>
<meta charset="utf-8">
<title>Brackenford Fluidworks</title>
<link href="https://fonts.googleapis.com/css2?family=Lato:wght@400;700;900&family=Open+Sans:ital,wght@0,400;0,600;0,700;1,400&display=swap" rel="stylesheet">
<style>
:root{
  --red:#ec1f27;
  --red-deep:#c5141b;
  --white:#ffffff;
  --grey:#aaaaaa;
  --ink:#222222;
  --text:#555555;
  --panel:#5a5a5a;
  --light:#f2f2f2;
  --tab:#ececec;
  --footer:#1f1f1f;
  --footer-bar:#141414;
}
*{margin:0;padding:0;box-sizing:border-box}
html,body{width:1200px;height:3255px;overflow:hidden}
body{font-family:"Open Sans",Arial,sans-serif;color:var(--ink);background:var(--white);position:relative}
a{color:inherit;text-decoration:none}
ul{list-style:none}

/* header */
.site-header{position:absolute;top:0;left:0;width:1200px;height:115px}
.brand{position:absolute;left:98px;top:22px;display:flex;align-items:center;gap:12px}
.brand-dot{width:58px;height:58px;border-radius:50%;background:var(--red)}
.brand-name{font-family:"Open Sans",sans-serif;font-weight:700;font-size:17px;line-height:1.15;color:var(--red);width:120px}
.header-contact{position:absolute;right:100px;top:22px;display:flex;gap:44px;font-size:15px;font-weight:600}
.header-contact span{display:flex;align-items:center;gap:12px}
.ring{width:30px;height:30px;border:2px solid var(--red);border-radius:50%;display:flex;align-items:center;justify-content:center}
.main-nav{position:absolute;right:100px;top:68px;display:flex;gap:22px;font-size:15px;font-weight:600;align-items:center;text-transform:uppercase}

/* hero */
.hero{position:absolute;top:115px;left:0;width:1200px;height:537px;background:linear-gradient(180deg,#5b5b5b 0%,#3a3a3a 45%,#1e1e1e 100%);color:var(--white);text-align:center}
.hero-title{position:absolute;top:120px;width:100%;font-family:"Lato",sans-serif;font-weight:700;font-size:98px;letter-spacing:2px;line-height:1}
.hero-sub{position:absolute;top:222px;width:100%;font-family:"Lato",sans-serif;font-size:46px;letter-spacing:12px;line-height:1}
.hero-line{position:absolute;top:278px;width:100%;font-size:21px;line-height:30px;font-weight:600}
.btn-red{display:inline-block;background:var(--red);color:var(--white);border:2px solid var(--white);border-radius:10px;font-weight:600;font-size:17px;padding:10px 30px}
.hero .btn-red{position:absolute;top:360px;left:514px}
.dots{position:absolute;top:480px;left:568px;display:flex;gap:6px}
.dots i{width:9px;height:9px;border:1px solid var(--white);display:block}
.dots i:first-child{background:var(--white)}

/* why */
.section-title{font-size:26px;font-weight:400;text-align:center;color:var(--ink)}
.why{position:absolute;top:728px;left:0;width:1200px}
.why-grid{display:flex;justify-content:center;gap:0;margin-top:52px}
.why-item{width:262px;text-align:center}
.why-item svg{height:44px}
.why-item h3{font-size:16px;font-weight:600;margin-top:10px;text-transform:uppercase}
.why-item p{font-size:14px;line-height:26px;color:var(--text);margin-top:14px}
.read-link{display:inline-block;margin-top:14px;font-size:13px;color:var(--red);text-decoration:underline}

/* about */
.about-panel{position:absolute;left:98px;top:1098px;width:480px;height:350px;background:linear-gradient(135deg,#666 0%,#555 60%,#4c4c4c 100%);color:var(--white);padding:28px 34px}
.about-panel h2{font-size:26px;font-weight:400}
.about-panel p{font-size:13.3px;line-height:28px;margin-top:14px}
.about-panel .btn-small{margin-top:16px}
.btn-small{display:inline-block;background:var(--red);color:var(--white);font-size:13px;font-weight:600;padding:7px 18px;border-radius:16px}
.about-photo{position:absolute;left:576px;top:1064px;width:526px;height:420px;background:linear-gradient(180deg,#7e8a93 0%,#9a8f7e 40%,#6f5f47 100%);border:2px solid #ddd}

/* band */
.band{position:absolute;top:1568px;left:0;width:1200px;height:307px;background:linear-gradient(90deg,#d71c23 0%,var(--red) 45%,#b71419 100%);color:var(--white);text-align:center}
.band h2{margin-top:73px;font-size:26px;font-weight:400}
.band p{font-size:17px;font-style:italic;line-height:28px;margin-top:12px}
.btn-outline{display:inline-flex;align-items:center;gap:10px;margin-top:18px;border:2px solid var(--white);border-radius:20px;padding:7px 28px;font-weight:600;font-size:17px}

/* services */
.services{position:absolute;top:1950px;left:0;width:1200px;height:650px}
.tabs{position:absolute;top:55px;left:102px;width:998px;height:36px;background:var(--tab);display:flex;justify-content:space-around;align-items:center;font-size:13.5px;font-weight:600;text-transform:uppercase}
.tabs .tab-active{position:relative}
.tabs .tab-active::before{content:"";position:absolute;top:-14px;left:50%;margin-left:-6px;border:6px solid transparent;border-top-color:#333}
.slide-side{position:absolute;top:235px;width:154px;height:233px}
.slide-left{left:0;background:linear-gradient(135deg,#b9a88a,#8a7a64 60%,#c9482f)}
.slide-right{left:1046px;background:linear-gradient(135deg,#6a5a44,#a08b6a 60%,#3a352e)}
.slide-photo{position:absolute;top:137px;left:224px;width:396px;height:428px;background:linear-gradient(160deg,#4c4a40 0%,#c9b21a 35%,#e6cf1f 60%,#3b3a34 100%);border:2px solid #ddd}
.slide-card{position:absolute;top:183px;left:620px;width:358px;height:337px;background:var(--panel);color:var(--white);padding:58px 24px 0 22px}
.slide-card p{font-size:13.3px;line-height:28px}
.slide-card .btn-small{margin-top:18px}

/* quote */
.quote{position:absolute;top:2602px;left:0;width:1200px;height:351px;background:var(--light);text-align:center}
.quote blockquote{margin-top:54px;font-size:16px;font-style:italic}
.quote h2{margin-top:16px;font-size:22px;font-weight:400}
.connect{margin:36px auto 0;width:800px;display:flex;align-items:center;gap:24px;font-size:13px;color:var(--grey)}
.connect::before,.connect::after{content:"";flex:1;height:1px;background:#d8d8d8}
.social{display:flex;justify-content:center;gap:22px;margin-top:22px}
.social span{width:44px;height:44px;border-radius:50%;background:var(--red)}
.social span:nth-child(even){background:#333}

/* footer */
.site-footer{position:absolute;top:2953px;left:0;width:1200px;height:257px;background:linear-gradient(120deg,#262626 0%,#1a1a1a 60%,#222 100%);color:var(--white)}
.footer-brand{position:absolute;left:98px;top:60px;width:190px;text-align:center}
.footer-brand .brand-dot{background:var(--white);margin:0 auto 14px;width:82px;height:82px}
.footer-brand span{font-weight:700;font-size:20px;line-height:1.2}
.footer-col{position:absolute;top:56px}
.footer-col h4{font-size:20px;font-weight:400;text-transform:uppercase}
.footer-col ul{margin-top:18px;font-size:13.5px}
.footer-col li{line-height:28px}
.bullets li::before{content:"";display:inline-block;width:6px;height:6px;border-radius:50%;background:var(--white);margin-right:14px;vertical-align:middle}
.col-links{left:342px}
.col-links ul{display:grid;grid-template-columns:150px 130px}
.col-care{left:633px}
.col-contact{left:872px}
.col-contact li{display:flex;gap:14px;align-items:flex-start;width:260px}
.col-contact svg{flex:none;margin-top:7px}
.footer-bar{position:absolute;top:3210px;left:0;width:1200px;height:45px;background:var(--footer-bar);color:#ddd;font-size:13px;text-align:center;line-height:45px}
</style>
</head>
<body>

<header class="site-header">
  <a class="brand" href="#"><span class="brand-dot"></span><span class="brand-name">Brackenford Fluidworks</span></a>
  <div class="header-contact">
    <span><i class="ring"><svg width="14" height="14" viewBox="0 0 24 24"><path fill="#ec1f27" d="M6.6 10.8a15 15 0 006.6 6.6l2.2-2.2c.3-.3.7-.4 1-.2 1.1.4 2.3.6 3.6.6.6 0 1 .4 1 1V20c0 .6-.4 1-1 1A17 17 0 013 4c0-.6.4-1 1-1h3.5c.6 0 1 .4 1 1 0 1.3.2 2.5.6 3.6.1.3 0 .7-.2 1z"/></svg></i>555 014 2290</span>
    <span><i class="ring"><svg width="14" height="14" viewBox="0 0 24 24"><path fill="none" stroke="#ec1f27" stroke-width="2.4" d="M12 3a9 9 0 100 18M16 12a4 4 0 11-4-4 4 4 0 014 4v1.5a2.5 2.5 0 005 0V12a9 9 0 00-9-9"/></svg></i>info@brackenfordfluid.com</span>
  </div>
  <nav class="main-nav">
    <a href="#">Home</a><a href="#">About Us</a><a href="#">Services</a><a href="#">Our Work</a><a href="#">Our Project</a><a href="#">Blog</a><a href="#">Contact Us</a>
    <svg width="14" height="14" viewBox="0 0 24 24"><circle cx="10" cy="10" r="7" fill="none" stroke="#222" stroke-width="3"/><path d="M15 15l7 7" stroke="#222" stroke-width="3"/></svg>
  </nav>
</header>

<section class="hero" role="img" aria-label="Workshop floor with a row of repaired black hydraulic cylinders">
  <h1 class="hero-title">BRACKENFORD</h1>
  <div class="hero-sub">FLUIDWORKS</div>
  <p class="hero-line">we can repair or replace any job.<br>There is not a job too big or too small, we service them all.</p>
  <a class="btn-red" href="#">Contact Now</a>
  <div class="dots"><i></i><i></i><i></i><i></i></div>
</section>

<section class="why">
  <h2 class="section-title">Why Choose Us</h2>
  <div class="why-grid">
    <div class="why-item">
      <svg viewBox="0 0 50 44" width="50"><g fill="#ec1f27"><circle cx="18" cy="26" r="12"/><circle cx="37" cy="12" r="8"/><circle cx="38" cy="34" r="6"/></g><g fill="#fff"><circle cx="18" cy="26" r="4.5"/><circle cx="37" cy="12" r="3"/><circle cx="38" cy="34" r="2.2"/></g><g stroke="#ec1f27" stroke-width="4"><path d="M18 11v30M3 26h30M7.5 15.5l21 21M28.5 15.5l-21 21"/></g><circle cx="18" cy="26" r="4.5" fill="#fff"/></svg>
      <h3>Quality</h3>
      <p>Lorem ipsum dolor sit amet,<br>consectetur adipiscing elit, sed do</p>
      <a class="read-link" href="#">Read More</a>
    </div>
    <div class="why-item">
      <svg viewBox="0 0 30 44" width="30"><text x="15" y="38" text-anchor="middle" font-family="Open Sans,sans-serif" font-weight="700" font-size="44" fill="#ec1f27">$</text></svg>
      <h3>Pricing</h3>
      <p>Lorem ipsum dolor sit amet,<br>consectetur adipiscing elit, sed do</p>
      <a class="read-link" href="#">Read More</a>
    </div>
    <div class="why-item">
      <svg viewBox="0 0 48 44" width="48"><g stroke="#ec1f27" stroke-linecap="round"><path d="M8 38L30 14" stroke-width="7"/><path d="M14 10l24 28" stroke-width="6"/></g><circle cx="33" cy="11" r="9" fill="#ec1f27"/><rect x="30" y="0" width="7" height="10" fill="#fff"/><rect x="8" y="4" width="10" height="8" fill="#ec1f27"/></svg>
      <h3>Services</h3>
      <p>Lorem ipsum dolor sit amet,<br>consectetur adipiscing elit, sed do</p>
      <a class="read-link" href="#">Read More</a>
    </div>
    <div class="why-item">
      <svg viewBox="0 0 44 44" width="44"><path d="M4 24l12 12L40 10" fill="none" stroke="#ec1f27" stroke-width="9"/></svg>
      <h3>Delivery</h3>
      <p>Lorem ipsum dolor sit amet,<br>consectetur adipiscing elit, sed do</p>
      <a class="read-link" href="#">Read More</a>
    </div>
  </div>
</section>

<div class="about-panel">
  <h2>About Us</h2>
  <p>Brackenford Fluidworks is a full hydraulic repair facility. We have 2 shops. We repair and service all hydraulic cylinders, pneumatic cylinders, hydraulic pumps, motors, valves and gearboxes. Our services range from large industrial plants to the individual that owns one piece of equipment. We also offer removal and install of cylinders. Along with free pick up and delivery, within a certain distance which is usually 100 miles from one of our shops.</p>
  <a class="btn-small" href="#">Read More</a>
</div>
<div class="about-photo" role="img" aria-label="Yellow hydraulic cylinder strapped to a flatbed trailer outside the shop"></div>

<section class="band" role="img" aria-label="Red-toned close-up of cylinder parts behind the call to action">
  <h2>We Can Repair or Replace any Job</h2>
  <p>Along with free pick up and delivery,<br>within a certain distance which is usually 100 miles from one of our shops.</p>
  <a class="btn-outline" href="#"><svg width="15" height="15" viewBox="0 0 24 24"><path fill="#fff" d="M6.6 10.8a15 15 0 006.6 6.6l2.2-2.2c.3-.3.7-.4 1-.2 1.1.4 2.3.6 3.6.6.6 0 1 .4 1 1V20c0 .6-.4 1-1 1A17 17 0 013 4c0-.6.4-1 1-1h3.5c.6 0 1 .4 1 1 0 1.3.2 2.5.6 3.6.1.3 0 .7-.2 1z"/></svg>Call Us 555 014 2290</a>
</section>

<section class="services">
  <h2 class="section-title">We Repair and Service</h2>
  <div class="tabs">
    <span class="tab-active">Hydraulic Cylinders</span><span>Pneumatic Cylinders</span><span>Hydraulic Pumps</span><span>Motors</span><span>Valves</span><span>Gearboxes</span>
  </div>
  <div class="slide-side slide-left" role="img" aria-label="Red hydraulic cylinder on a workbench"></div>
  <div class="slide-photo" role="img" aria-label="Close-up of a freshly painted yellow hydraulic cylinder with shop label"></div>
  <div class="slide-card">
    <p>But I must explain to you how all this mistaken idea of denouncing pleasure and praising pain was born and I will give you a complete account of the system, and expound the actual teachings of the great explorer of the truth, the builder of human happiness. No one rejects.</p>
    <a class="btn-small" href="#">Read More</a>
  </div>
  <div class="slide-side slide-right" role="img" aria-label="Gearbox assembly on a wooden pallet"></div>
</section>

<section class="quote">
  <blockquote>“With over 30 years experience in the hydraulic business”</blockquote>
  <h2>There is not a job too big or too small, we service them all</h2>
  <div class="connect">Connect with us</div>
  <div class="social" aria-label="Social links"><span></span><span></span><span></span><span></span><span></span></div>
</section>

<footer class="site-footer">
  <div class="footer-brand"><div class="brand-dot"></div><span>Brackenford Fluidworks</span></div>
  <div class="footer-col col-links">
    <h4>Quick Links</h4>
    <ul class="bullets"><li>Home</li><li>Our Projects</li><li>About Us</li><li>Blog</li><li>Services</li><li>Contact Us</li><li>Our Work</li></ul>
  </div>
  <div class="footer-col col-care">
    <h4>Customer Care</h4>
    <ul class="bullets"><li>Customer Service</li><li>Warranty Policy</li><li>Installation and use</li><li>Repair</li></ul>
  </div>
  <div class="footer-col col-contact">
    <h4>Contact Us</h4>
    <ul>
      <li><svg width="12" height="14" viewBox="0 0 24 28"><path fill="#fff" d="M12 0a10 10 0 00-10 10c0 8 10 18 10 18s10-10 10-18A10 10 0 0012 0zm0 14a4 4 0 110-8 4 4 0 010 8z"/></svg><span>Brackenford Fluidworks, 48 Millrace Road, Unit 6</span></li>
      <li><svg width="14" height="12" viewBox="0 0 24 18"><path fill="#fff" d="M0 0h24v18H0z"/><path d="M0 0l12 9 12-9" fill="none" stroke="#1f1f1f" stroke-width="2"/></svg><span>info@brackenfordfluid.com</span></li>
      <li><svg width="14" height="14" viewBox="0 0 24 24"><path fill="#fff" d="M6.6 10.8a15 15 0 006.6 6.6l2.2-2.2c.3-.3.7-.4 1-.2 1.1.4 2.3.6 3.6.6.6 0 1 .4 1 1V20c0 .6-.4 1-1 1A17 17 0 013 4c0-.6.4-1 1-1h3.5c.6 0 1 .4 1 1 0 1.3.2 2.5.6 3.6.1.3 0 .7-.2 1z"/></svg><span>555 014 2290</span></li>
    </ul>
  </div>
</footer>
<div class="footer-bar">© 2018 Brackenford Fluidworks. All rights reserved.</div>

</body>
</html>
```